Business card design for Virtual Assistance company

I need a business card designed for my virtual assistance company. We are a small company who services primarily C-level executive clients. The card needs to be double sided with the following contact information on the back:
Melissa Thornbury
Owner/CEO
info@rkpadvisory.net
www.rkpadvisory.net
555.302.9817

The front side should just have the company name incorporated: "RKP Advisory" and "virtual assistance"

The card should be simplistic, but eye catching and should speak to high level executives. Our primary focus areas consist of executive assistance and government contracting.

Target Market(s)

CEOs and executives

Contact Information for Business Card

see project description. phone, email, website.

Colors

Designer to choose only greyscale colors for use in the design.

```html
<!DOCTYPE html>
<html lang="en">
<head>
<meta charset="utf-8">
<title>RKP Advisory – Business Card</title>
<link rel="stylesheet" href="https://fonts.googleapis.com/css2?family=Cinzel:wght@600;700&family=Poppins:wght@400;500&display=swap">
<style>
  :root {
    --backdrop: #9b9b9b;
    --charcoal: #2b2b2b;
    --white: #ffffff;
    --ink: #333333;
    --muted: #8c8c8c;
    --rule: #c4c4c4;
  }
  * { margin: 0; padding: 0; box-sizing: border-box; }
  html, body {
    width: 1093px; height: 1200px; overflow: hidden;
    background: var(--backdrop);
  }
  .canvas { position: relative; width: 1093px; height: 1200px; }

  .card {
    position: absolute; left: 265px;
    width: 578px; height: 356px;
    border-radius: 26px;
  }
  .card--front { top: 226px; background: var(--white); }
  .card--back  { top: 621px; background: var(--charcoal); }

  /* brand lockup */
  .brand {
    position: absolute; display: flex; flex-direction: column; align-items: center;
    font-family: "Cinzel", serif; font-weight: 700; line-height: 1;
  }
  .brand__initials { letter-spacing: 1px; }
  .brand__word { letter-spacing: 1px; }
  .brand__tagline {
    display: flex; align-items: center; gap: 6px;
    font-family: "Poppins", sans-serif; font-weight: 500; letter-spacing: 2px;
    line-height: 1.5;
  }
  .brand__tagline::before, .brand__tagline::after {
    content: ""; display: block; height: 1.5px; background: currentColor;
  }

  .card--front .brand { left: 49px; top: 103px; width: 220px; color: var(--charcoal); }
  .card--front .brand__initials { font-size: 90px; }
  .card--front .brand__word { font-size: 33px; margin-top: 7px; }
  .card--front .brand__tagline { font-size: 10px; color: var(--muted); margin-top: 1px; }
  .card--front .brand__tagline::before, .card--front .brand__tagline::after { width: 22px; }

  .card--back .brand { left: 139px; top: 73px; width: 300px; color: var(--white); }
  .card--back .brand__initials { font-size: 130px; }
  .card--back .brand__word { font-size: 49px; margin-top: 6px; }
  .card--back .brand__tagline { font-size: 15px; color: var(--white); margin-top: 0; }
  .card--back .brand__tagline::before, .card--back .brand__tagline::after { width: 29px; }

  .divider {
    position: absolute; left: 288px; top: 74px;
    width: 1.5px; height: 210px; background: var(--rule);
  }

  .contact { position: absolute; left: 310px; top: 108px; }
  .contact__name {
    font-family: "Cinzel", serif; font-weight: 700; font-size: 19.5px;
    color: var(--charcoal); letter-spacing: .3px; line-height: 1;
  }
  .contact__title {
    font-family: "Poppins", sans-serif; font-size: 17.5px; color: var(--ink);
    line-height: 1; margin-top: 4px;
  }
  .contact__list { list-style: none; margin-top: 28px; }
  .contact__item {
    display: flex; align-items: center; gap: 7px; height: 21px;
    font-family: "Poppins", sans-serif; font-size: 18px; color: var(--ink);
  }
  .contact__item svg { width: 16px; height: 16px; flex: none; fill: var(--charcoal); }
</style>
</head>
<body>
<main class="canvas">

  <section class="card card--front" aria-label="Business card front">
    <div class="brand">
      <span class="brand__initials">RKP</span>
      <span class="brand__word">ADVISORY</span>
      <span class="brand__tagline">VIRTUAL ASSISTANCE</span>
    </div>

    <div class="divider"></div>

    <div class="contact">
      <p class="contact__name">MELISSA THORNBURY</p>
      <p class="contact__title">Owner/CEO</p>
      <ul class="contact__list">
        <li class="contact__item">
          <svg viewBox="0 0 24 24" aria-hidden="true"><path d="M6.6 10.8a15.1 15.1 0 0 0 6.6 6.6l2.2-2.2a1 1 0 0 1 1-.25 11.4 11.4 0 0 0 3.6.57 1 1 0 0 1 1 1V20a1 1 0 0 1-1 1A17 17 0 0 1 3 4a1 1 0 0 1 1-1h3.5a1 1 0 0 1 1 1c0 1.25.2 2.45.57 3.57a1 1 0 0 1-.25 1z"/></svg>
          555.302.9817
        </li>
        <li class="contact__item">
          <svg viewBox="0 0 24 24" aria-hidden="true"><path d="M2 5h20v14H2z" fill="var(--charcoal)"/><path d="M3 6l9 7 9-7" fill="none" stroke="#fff" stroke-width="1.5"/></svg>
          info@rkpadvisory.net
        </li>
        <li class="contact__item">
          <svg viewBox="0 0 24 24" aria-hidden="true"><circle cx="12" cy="12" r="9.5" fill="none" stroke="var(--charcoal)" stroke-width="2"/><ellipse cx="12" cy="12" rx="4" ry="9.5" fill="none" stroke="var(--charcoal)" stroke-width="1.6"/><path d="M2.5 12h19M4 7.5h16M4 16.5h16" stroke="var(--charcoal)" stroke-width="1.4"/></svg>
          www.rkpadvisory.net
        </li>
      </ul>
    </div>
  </section>

  <section class="card card--back" aria-label="Business card back">
    <div class="brand">
      <span class="brand__initials">RKP</span>
      <span class="brand__word">ADVISORY</span>
      <span class="brand__tagline">VIRTUAL ASSISTANCE</span>
    </div>
  </section>

</main>
</body>
</html>
```